Business card

We need a business card design for our company based in Auckland , New Zealand called 'Ridge + Studio Ltd'. We provide architectural services. We would like to see designs that use the max. three colours (such as white, black, grey) The final design should communicate financial safety and growth."
Also I will provide our company logo. I would like to the logo to be embeded onto our business card.

Target Market(s)

new residential house, alteration & addition & light commericila design & drafting service

Industry/Entity Type

Architecture

Contact Information for Business Card

Company name: ridge + studio Ltd.
Name: Mark Delford
Job title: architectural designer & Design LBP
email address: mark@rplusd.co.nz
mobile number: 02 5163 2290
web site: www.rplusd.co.nz

Requirements
Must have
• My project must have..
• - embeded logo (attached company logo)
• I don't have a bigger version for our company logo, but I have one old one, so you can remove the word from it)
• - insert the attached small BKTW logo & LBP logo
• - creative, simple and clear business card.
• - Max. three colours
Nice to have
• - Here are the samples I would like to share with you: http://www.plimvora.com/blog/minimalistic-business-card-designs/
• I would like to have my business card like one of the creation.
Should not have
• TBA

```html
<!DOCTYPE html>
<html lang="en">
<head>
<meta charset="utf-8">
<title>Ridge + Studio Ltd — Business Card</title>
<link rel="stylesheet" href="https://fonts.googleapis.com/css2?family=Lato:wght@400;700;900&display=swap">
<style>
  :root {
    --bg: #3a3a3a;
    --card-dark: #0b0b0b;
    --card-light: #ffffff;
    --ink-light: #ffffff;
    --ink-soft: #d8d8d8;
    --ink-dark: #111111;
  }
  * { box-sizing: border-box; margin: 0; padding: 0; }
  html, body {
    width: 1200px; height: 950px; overflow: hidden;
    background: var(--bg);
    font-family: "Lato", Arial, sans-serif;
  }
  .stage { position: relative; width: 1200px; height: 950px; }
  .card {
    position: absolute; left: 330px; width: 540px; height: 330px;
    border-radius: 4px;
    box-shadow: 0 12px 28px rgba(0,0,0,.45);
  }
  .card-back { top: 90px; background: var(--card-dark); color: var(--ink-light); }
  .card-front { top: 500px; background: var(--card-light); color: var(--ink-dark); }

  .partner-marks {
    position: absolute; left: 40px; top: 40px;
    display: flex; align-items: center; gap: 16px;
  }
  .partner-name {
    font-weight: 900; font-size: 30px; letter-spacing: -1px; color: var(--ink-light);
  }
  .badge { width: 58px; height: 58px; }

  .contact {
    position: absolute; left: 250px; top: 150px; width: 270px;
  }
  .contact-name, .contact-title {
    font-weight: 700; font-size: 18px; line-height: 1.25;
  }
  .contact-company { font-size: 12px; color: var(--ink-soft); margin: 10px 0 8px; }
  .contact-list { list-style: none; font-size: 12px; color: var(--ink-soft); }
  .contact-list li { display: flex; align-items: center; gap: 8px; margin-bottom: 5px; }
  .contact-list svg { width: 12px; height: 12px; flex: none; }

  .brand {
    position: absolute; inset: 0;
    display: flex; align-items: center; justify-content: center;
  }
  .brand-name {
    font-weight: 700; font-size: 22px; letter-spacing: 1px; color: var(--ink-dark);
  }
</style>
</head>
<body>
<main class="stage">
  <section class="card card-back" aria-label="Card back">
    <div class="partner-marks">
      <span class="partner-name">BKTW</span>
      <svg class="badge" viewBox="0 0 58 58" role="img" aria-label="Licensed practitioner badge">
        <circle cx="29" cy="29" r="28" fill="#ffffff"/>
      </svg>
    </div>
    <div class="contact">
      <p class="contact-name">Mark Delford</p>
      <p class="contact-title">architectural designer &amp;<br>Design LBP</p>
      <p class="contact-company">ridge + studio Ltd.</p>
      <ul class="contact-list">
        <li>
          <svg viewBox="0 0 12 12" aria-hidden="true"><rect x="2" y="0.5" width="8" height="11" rx="1.2" fill="none" stroke="#fff" stroke-width="1.2"/></svg>
          02 5163 2290
        </li>
        <li>
          <svg viewBox="0 0 12 12" aria-hidden="true"><rect x="0.5" y="2" width="11" height="8" fill="#fff"/><path d="M0.5 2 L6 6.5 L11.5 2" fill="none" stroke="#000" stroke-width="1"/></svg>
          mark@rplusd.co.nz
        </li>
        <li>
          <svg viewBox="0 0 12 12" aria-hidden="true"><circle cx="6" cy="6" r="5.5" fill="#fff"/><path d="M0.5 6 H11.5 M6 0.5 V11.5" stroke="#000" stroke-width="0.9"/></svg>
          www.rplusd.co.nz
        </li>
      </ul>
    </div>
  </section>

  <section class="card card-front" aria-label="Card front">
    <div class="brand">
      <span class="brand-name">Ridge + Studio</span>
    </div>
  </section>
</main>
</body>
</html>
```